Tessaline Wellness Marketing Flyer

We are a new medical practice in the community and need a flyer to send to other medical offices to inform of our services. We just completed our logo with Draftmarketo and would like to incorporate that plus our marketing content into the flyer. Our medical practice has 2 divisions: (1)Mental Health/Psychiatry and (2) Migraine and Neurospasticity Management. Please see website for content and provider photos at www.TessaWellnet.com

Target Market(s)

Other Healthcare Professionals in the Community

Industry/Entity Type

Medical

Requirements
Must have
• Photos of all 5 healthcare providers, phone number, address, logo

```html
<!DOCTYPE html>
<html lang="en">
<head>
<meta charset="utf-8">
<title>Tessaline Wellness Flyer</title>
<link rel="stylesheet" href="https://fonts.googleapis.com/css2?family=Playfair+Display:ital,wght@0,600;0,700;1,600&family=Open+Sans:ital,wght@0,400;0,600;0,700;1,400;1,600&display=swap">
<style>
:root{
  --teal:#0aa79c;
  --teal-light:#19cfc0;
  --green:#a7e05a;
  --ink:#2b2b2b;
  --muted:#4a4a4a;
  --cream:#f9f9f1;
  --stage:#2a3038;
  --rule:#bdbdbd;
}
*{margin:0;padding:0;box-sizing:border-box}
html,body{width:1200px;height:2646px;overflow:hidden;background:var(--stage)}
.flyer{position:absolute;left:134px;top:720px;width:932px;height:1206px;background:#fff;overflow:hidden;font-family:"Open Sans",Arial,sans-serif;color:var(--ink)}
.flyer-bg{position:absolute;left:0;top:0}
.hero-photo{position:absolute;left:0;top:0}

.brand{position:absolute;left:102px;top:80px;width:318px;text-align:center}
.brand-mark{width:100px;height:100px;border-radius:50%;background:var(--teal);margin:0 auto 10px}
.brand-name{font-family:"Playfair Display",Georgia,serif;font-weight:600;font-size:36px;line-height:40px;color:var(--teal);letter-spacing:1px}

.headline{position:absolute;left:98px;top:300px;font-family:"Playfair Display",Georgia,serif;font-weight:700;font-size:56px;line-height:54px;color:#fff}
.subline{position:absolute;left:98px;top:480px;font-size:20px;line-height:20px;color:#fff;font-weight:600}

.services{position:absolute;left:102px;top:655px;width:383px}
.service{position:relative;padding-left:82px;height:98px}
.service svg{position:absolute;left:0;top:6px}
.service h3{font-size:17px;line-height:23px;font-weight:700;color:var(--ink);margin-bottom:3px}
.service p{font-size:12.8px;line-height:15.5px;color:var(--muted);text-align:justify}

.stories{position:absolute;left:110px;top:942px;width:375px}
.stories h2{font-family:"Playfair Display",Georgia,serif;font-weight:700;font-size:36px;line-height:43px;color:var(--teal);margin-bottom:10px}
.stories .quote-mark{position:absolute;right:6px;top:-18px;font-family:"Playfair Display",Georgia,serif;font-style:italic;font-size:120px;color:#e4e4de;line-height:1}
.stories blockquote{font-style:italic;font-size:13px;line-height:19px;color:var(--muted);position:relative}
.stories cite{display:block;text-align:right;font-style:normal;font-weight:700;font-size:12.5px;margin-top:12px;color:var(--ink)}

.providers{position:absolute;left:540px;top:558px;width:303px}
.providers h2{font-family:"Playfair Display",Georgia,serif;font-weight:700;font-size:37px;line-height:35px;color:var(--teal)}
.providers p{font-size:13px;line-height:16px;color:var(--muted);margin-top:6px}

.roster{position:absolute;left:543px;top:771px;width:293px}
.roster-row{display:flex;align-items:center;height:87px;border-bottom:1.5px dashed var(--rule)}
.provider{display:flex;align-items:center;width:160px}
.provider + .provider{width:auto}
.provider-photo{width:68px;height:68px;border-radius:50%;background:radial-gradient(circle at 50% 40%,#cfc6bd,#6f7c86);flex:none}
.provider-name{font-family:"Playfair Display",Georgia,serif;font-size:12px;line-height:11.5px;margin-left:8px;color:var(--ink)}

.portal{position:absolute;left:558px;top:1044px;font-style:italic;font-weight:600;font-size:31px;line-height:30px;color:#111}

.footer{position:absolute;left:0;top:1125px;width:932px;height:81px;display:flex;color:#fff;font-size:18px}
.footer-cell{display:flex;align-items:center;justify-content:center;gap:6px}
.footer .phone{margin-left:166px;width:197px;background:var(--green);font-weight:700}
.footer .web{width:249px;background:var(--teal)}
.footer .address{flex:1;background:var(--green);font-size:14px;line-height:15px;justify-content:flex-start;padding-left:14px}
</style>
</head>
<body>
<main class="flyer">
  <svg class="flyer-bg" width="932" height="1206" viewBox="0 0 932 1206" aria-hidden="true">
    <defs>
      <linearGradient id="band" x1="0" y1="0" x2="1" y2="0">
        <stop offset="0" stop-color="#19cfc0"/><stop offset="1" stop-color="#06a097"/>
      </linearGradient>
    </defs>
    <rect x="0" y="600" width="511" height="525" fill="#f9f9f1"/>
    <path d="M0 286 H520 L570 480 Q580 500 600 496 L760 470 L0 641 Z" fill="url(#band)"/>
    <path d="M0 1206 H160 V1116 Q160 1076 120 1076 H0 Z" fill="#0aa79c"/>
  </svg>

  <svg class="hero-photo" width="932" height="510" viewBox="0 0 932 510" role="img" aria-label="Photo of a smiling woman in a yellow top looking at her phone in a bright living room">
    <defs>
      <linearGradient id="photo" x1="0" y1="0" x2="1" y2="1">
        <stop offset="0" stop-color="#f1eee9"/><stop offset=".6" stop-color="#e2dcd4"/><stop offset="1" stop-color="#d8b84c"/>
      </linearGradient>
    </defs>
    <path d="M493 0 H932 V427 L600 500 Q575 505 568 480 Z" fill="url(#photo)"/>
  </svg>

  <div class="brand">
    <div class="brand-mark"></div>
    <div class="brand-name">Tessaline Wellness</div>
  </div>

  <h1 class="headline">Helping Bodies<br>Helping Minds<br>Helping You</h1>
  <p class="subline">Mental Health and Psychiatry Services<br>Migraine and Neurospasticity Intervention</p>

  <section class="services">
    <div class="service">
      <svg width="66" height="42" viewBox="0 0 66 42" aria-hidden="true"><path d="M33 3C16 3 3 10 3 19c0 6 5 10 12 13l-6 8 14-6c3 1 6 1 10 1 17 0 30-7 30-16S50 3 33 3Z" fill="none" stroke="#333" stroke-width="2"/><circle cx="22" cy="19" r="2.6" fill="#333"/><circle cx="33" cy="19" r="2.6" fill="#333"/><circle cx="44" cy="19" r="2.6" fill="#333"/></svg>
      <h3>NEW PATIENT EVALUATION</h3>
      <p>Consults provided for evaluation and management of patients with chronic migraines or neurospasticity challenges.</p>
    </div>
    <div class="service">
      <svg width="58" height="54" viewBox="0 0 58 54" aria-hidden="true"><path d="M4 3h30v48H4Z M10 12h18 M10 19h18 M10 26h18" fill="none" stroke="#333" stroke-width="2"/><path d="M44 14h8v34l-4 5-4-5Z M44 20h-5" fill="none" stroke="#333" stroke-width="2"/></svg>
      <h3>INSURANCE PRE-AUTHORIZATION</h3>
      <p>Botulinum toxin injections may be a recommended treatment option. If so, our office completes insurance pre-authorizations on your</p>
    </div>
    <div class="service">
      <svg width="56" height="46" viewBox="0 0 56 46" aria-hidden="true"><path d="M2 8h52v36H2Z M2 16h52 M2 25h52 M2 34h52 M12 16v28 M22 16v28 M32 16v28 M42 16v28 M10 3v9 M20 3v9 M30 3v9 M40 3v9" fill="none" stroke="#333" stroke-width="2"/></svg>
      <h3>INSURANCE PRE-AUTHORIZATION</h3>
      <p>Timely appointments following insurance approval are available to quickly get you on the road to relief.</p>
    </div>
  </section>

  <section class="stories">
    <span class="quote-mark" aria-hidden="true">&rdquo;</span>
    <h2>Patient Stories</h2>
    <blockquote>Owen is great with kids! My son was nervous to see him but after the appointment was asking when he could go back. Owen really engaged and listened to him, he valued what he had to say and listened to our concerns as parents.
      <cite>LENA, MOTHER OF 3</cite>
    </blockquote>
  </section>

  <section class="providers">
    <h2>Meet Our<br>Mental Health<br>Providers</h2>
    <p>Bringing comprehensive evaluation, medication management and psychotherapy to the full spectrum of mental health disorders including minor, moderate and major depression, bipolar disorder, ADD/ADHD, anxiety, schizophrenia, stress or grief reactions, and others.</p>
  </section>

  <div class="roster">
    <div class="roster-row">
      <div class="provider"><div class="provider-photo" role="img" aria-label="Provider portrait"></div><span class="provider-name">Alden Marsh,<br>PMHNP -<br>BC</span></div>
      <div class="provider"><div class="provider-photo" role="img" aria-label="Provider portrait"></div><span class="provider-name">Dr. Calvin<br>Orrick</span></div>
    </div>
    <div class="roster-row">
      <div class="provider"><div class="provider-photo" role="img" aria-label="Provider portrait"></div><span class="provider-name">Alden Marsh,<br>PMHNP -<br>BC</span></div>
      <div class="provider"><div class="provider-photo" role="img" aria-label="Provider portrait"></div><span class="provider-name">Owen Tarrant<br>PMHNP -<br>BC</span></div>
    </div>
    <div class="roster-row">
      <div class="provider"><div class="provider-photo" role="img" aria-label="Provider portrait"></div><span class="provider-name">Maren Holloway,<br>PMHNP - BC</span></div>
    </div>
  </div>

  <p class="portal">Join us<br>on the Portal!</p>

  <footer class="footer">
    <div class="footer-cell phone">
      <svg width="16" height="16" viewBox="0 0 24 24" aria-hidden="true"><path d="M6.6 10.8a15 15 0 0 0 6.6 6.6l2.2-2.2c.3-.3.7-.4 1-.2 1.1.4 2.3.6 3.6.6.6 0 1 .4 1 1V20c0 .6-.4 1-1 1A17 17 0 0 1 3 4c0-.6.4-1 1-1h3.5c.6 0 1 .4 1 1 0 1.3.2 2.5.6 3.6.1.3 0 .7-.2 1Z" fill="none" stroke="#fff" stroke-width="2"/></svg>
      555-014-2870
    </div>
    <div class="footer-cell web">
      <svg width="16" height="16" viewBox="0 0 24 24" aria-hidden="true"><circle cx="12" cy="12" r="10" fill="none" stroke="#fff" stroke-width="2"/><path d="M2 12h20M12 2c3 3 3 17 0 20M12 2c-3 3-3 17 0 20" fill="none" stroke="#fff" stroke-width="2"/></svg>
      www.TessaWellnet.com
    </div>
    <div class="footer-cell address">
      <svg width="14" height="20" viewBox="0 0 14 20" aria-hidden="true"><path d="M7 1a6 6 0 0 1 6 6c0 5-6 12-6 12S1 12 1 7a6 6 0 0 1 6-6Z" fill="#fff"/><circle cx="7" cy="7" r="2.3" fill="#a7e05a"/></svg>
      <span>412 W. Larchmont Ave, Suite B<br>Brookhaven, ID 83900</span>
    </div>
  </footer>
</main>
</body>
</html>
```